Healthcare and Professional IT Services Company need a redesigned business card

We are a IT Services company that targets small medical practices and professional business such as Attorneys, Accounts, Architects etc. We want to communicate a professional yet friendly image using recent logo redesign here on ArtHarbor. Like to see the colors blue and orange in the design. Must use the Tall Pine Computing as displayed in the new logo - then also want to incorporate the fish logo as well.

Target Market(s)

Small medical and professional services

Industry/Entity Type

It Company

Contact Information for Business Card

The usual stuff, place for name address phone website. Also maybe our tagline which is "Rooted in reliable IT"

Requirements
Must have
• My new logo and the fish somewhere on the card

```html
<!DOCTYPE html>
<html lang="en">
<head>
<meta charset="utf-8">
<title>Tall Pine Computing – Business Card</title>
<link rel="stylesheet" href="https://fonts.googleapis.com/css2?family=Lato:wght@400;700&display=swap">
<style>
  :root {
    --backdrop: #2b2b2b;
    --brand-blue: #1a84cc;
    --brand-blue-deep: #1274b8;
    --brand-blue-light: #3f9ad8;
    --paper: #ffffff;
    --accent-orange: #f39a2b;
    --ink-light: #ffffff;
  }
  * { margin: 0; padding: 0; box-sizing: border-box; }
  html, body {
    width: 1200px;
    height: 659px;
    overflow: hidden;
    background: var(--backdrop);
    font-family: "Lato", Arial, sans-serif;
  }
  .stage {
    position: relative;
    width: 1200px;
    height: 659px;
    display: flex;
    align-items: center;
    justify-content: center;
    gap: 40px;
  }
  .card {
    position: relative;
    width: 520px;
    height: 298px;
    overflow: hidden;
    border-radius: 2px;
  }

  /* Front side */
  .card-front { background: var(--paper); }
  .card-front .panel-shape {
    position: absolute;
    inset: 0;
  }
  .brand-block {
    position: absolute;
    left: 24px;
    top: 50px;
    width: 250px;
    display: flex;
    flex-direction: column;
    align-items: center;
  }
  .mascot-area {
    width: 150px;
    height: 110px;
    border-radius: 50% 45% 40% 55%;
    background: radial-gradient(circle at 50% 45%, #d8ecf8, #bfe0f4);
  }
  .brand-name {
    margin-top: 16px;
    font-weight: 700;
    font-size: 24px;
    color: var(--brand-blue);
    text-align: center;
    line-height: 1.1;
    white-space: nowrap;
  }
  .brand-rule {
    margin-top: 10px;
    width: 150px;
    height: 2px;
    background: var(--accent-orange);
  }
  .contact-block {
    position: absolute;
    left: 330px;
    top: 50px;
    color: var(--ink-light);
  }
  .person-name { font-weight: 700; font-size: 20px; }
  .person-role { font-size: 13px; margin-top: 2px; }
  .address { font-size: 12px; line-height: 1.5; margin-top: 20px; }
  .contact-list { list-style: none; margin-top: 8px; font-size: 12px; line-height: 1.75; }
  .contact-list li { display: flex; align-items: center; gap: 7px; }
  .contact-list svg { width: 11px; height: 11px; flex: none; }

  /* Back side */
  .card-back { background: linear-gradient(160deg, var(--brand-blue-light), var(--brand-blue-deep)); }
  .mascot-banner {
    position: absolute;
    left: 0;
    top: 0;
    width: 300px;
    height: 200px;
    border-radius: 0 0 60% 0;
    background: linear-gradient(160deg, rgba(255,255,255,0.22), rgba(255,255,255,0.08));
  }
  .back-brand {
    position: absolute;
    right: 34px;
    bottom: 34px;
    text-align: right;
    color: var(--ink-light);
  }
  .back-brand .brand-name-light {
    font-weight: 700;
    font-size: 30px;
    line-height: 1.1;
    white-space: nowrap;
  }
  .tagline {
    margin-top: 8px;
    font-size: 15px;
    letter-spacing: 0.5px;
  }
</style>
</head>
<body>
<main class="stage">

  <section class="card card-front" aria-label="Business card front">
    <svg class="panel-shape" viewBox="0 0 520 298" width="520" height="298" aria-hidden="true">
      <path d="M300 0 H520 V298 H332 Q300 298 300 266 Z" fill="var(--brand-blue)"/>
      <path d="M290 0 V266 Q290 306 332 306" fill="none" stroke="var(--brand-blue)" stroke-width="2"/>
    </svg>

    <div class="brand-block">
      <div class="mascot-area" role="img" aria-label="Friendly fish mascot illustration"></div>
      <div class="brand-name">Tall Pine Computing</div>
      <div class="brand-rule"></div>
    </div>

    <div class="contact-block">
      <div class="person-name">Maya Torres</div>
      <div class="person-role">CEO/Founder</div>
      <div class="address">2150 Harbor View Road<br>Juneau, Alaska 99801</div>
      <ul class="contact-list">
        <li>
          <svg viewBox="0 0 12 12" aria-hidden="true"><path d="M2.5 1 L4.5 1 L5.2 3.5 L4 4.5 Q5 7 7.5 8 L8.5 6.8 L11 7.5 L11 9.5 Q10.5 11 9 11 Q1 10 1 2.5 Q1 1 2.5 1 Z" fill="#fff"/></svg>
          555 014 2290
        </li>
        <li>
          <svg viewBox="0 0 12 12" aria-hidden="true"><rect x="1" y="2.5" width="10" height="7" fill="#fff"/><path d="M1 2.5 L6 6.5 L11 2.5" fill="none" stroke="var(--brand-blue)" stroke-width="1"/></svg>
          hello@tallpine.example
        </li>
        <li>
          <svg viewBox="0 0 12 12" aria-hidden="true"><circle cx="6" cy="6" r="5" fill="#fff"/><path d="M1 6 H11 M6 1 Q3 6 6 11 Q9 6 6 1" fill="none" stroke="var(--brand-blue)" stroke-width="0.8"/></svg>
          www.tallpine.example
        </li>
      </ul>
    </div>
  </section>

  <section class="card card-back" aria-label="Business card back">
    <div class="mascot-banner" role="img" aria-label="Large outlined fish mascot decoration"></div>
    <div class="back-brand">
      <div class="brand-name-light">Tall Pine Computing</div>
      <div class="tagline">Rooted in reliable IT</div>
    </div>
  </section>

</main>
</body>
</html>
```